New letter head for Air Conditioning business

We need a new professional letter head design to suit our new re-branded air conditioning business. Our new logo is attached

```html
<!DOCTYPE html>
<html lang="en">
<head>
<meta charset="utf-8">
<title>Northwind Letterhead</title>
<link href="https://fonts.googleapis.com/css2?family=Poppins:wght@400;500;600;700&display=swap" rel="stylesheet">
<style>
  :root {
    --backdrop: #d6d6d6;
    --paper-top: #ebe8e9;
    --paper-mid: #f8f8f9;
    --paper-bottom: #ebe9ea;
    --ink: #141414;
    --brand-dark: #414042;
    --brand-green: #66c285;
    --rule: #6d6d6d;
    --signature-tone: #d9d7d8;
  }
  * { box-sizing: border-box; margin: 0; padding: 0; }
  html, body {
    width: 1200px; height: 1200px; overflow: hidden;
    background: var(--backdrop);
    font-family: "Poppins", sans-serif;
    color: var(--ink);
  }
  .letterhead {
    position: absolute; left: 190px; top: 20px;
    width: 820px; height: 1160px; overflow: hidden;
    background: linear-gradient(180deg, var(--paper-top) 0%, var(--paper-mid) 45%, var(--paper-mid) 60%, var(--paper-bottom) 100%);
  }
  .brand {
    position: absolute; top: 82px; left: 0; width: 100%;
    display: flex; justify-content: center; align-items: center; gap: 14px;
  }
  .brand-dot { width: 40px; height: 40px; border-radius: 50%; background: var(--brand-green); }
  .brand-name {
    font-weight: 600; font-size: 40px; letter-spacing: 4px;
    color: var(--brand-dark); line-height: 1;
  }
  .sender-name { position: absolute; left: 61px; top: 276px; font-size: 20px; font-weight: 600; }
  .letter-date { position: absolute; right: 51px; top: 276px; font-size: 20px; font-weight: 600; }
  .sender-address { position: absolute; left: 61px; top: 314px; font-size: 20px; font-weight: 500; }
  .letter-body {
    position: absolute; left: 55px; top: 352px; width: 714px;
    font-size: 15.4px; line-height: 19.2px; text-align: justify;
  }
  .letter-body p + p { margin-top: 27px; }
  .closing { position: absolute; left: 61px; top: 726px; font-size: 20px; font-weight: 500; }
  .signature {
    position: absolute; left: 55px; top: 782px; width: 172px; height: 58px;
    background: var(--signature-tone); border-radius: 4px;
  }
  .signer { position: absolute; left: 55px; top: 872px; font-size: 20px; font-weight: 500; line-height: 36px; }
  .footer-rule {
    position: absolute; left: 83px; top: 977px; width: 674px; height: 1.5px;
    background: var(--rule);
  }
  .contact { position: absolute; top: 1012px; display: flex; align-items: center; }
  .contact-icon { width: 43px; height: 43px; flex: none; }
  .contact-text { font-size: 19px; font-weight: 500; line-height: 22px; }
  .contact-phone { left: 65px; }
  .contact-phone .contact-text { margin-left: 17px; font-size: 20px; }
  .contact-web { left: 273px; top: 1014px; }
  .contact-web .contact-icon { width: 38px; height: 38px; }
  .contact-web .contact-text { margin-left: 17px; font-size: 17px; }
  .contact-mail { left: 552px; top: 1010px; }
  .contact-mail .contact-text { margin-left: 22px; font-size: 17px; margin-top: -12px; }
  .band-accent { position: absolute; left: 0; top: 1079px; width: 360px; height: 27px; }
  .band-base {
    position: absolute; left: 0; top: 1105px; width: 100%; height: 55px;
    background: var(--brand-dark);
  }
</style>
</head>
<body>
<main class="letterhead">
  <header class="brand">
    <span class="brand-dot"></span>
    <span class="brand-name">NORTHWIND</span>
  </header>

  <div class="sender-name">Your&nbsp; Name Here</div>
  <div class="letter-date">Date : 4.6.2021</div>
  <div class="sender-address">Address</div>

  <section class="letter-body">
    <p>Lorem ipsum dolor sit amet, consectetur adipiscing elit. Nam pretium quam eget feugiat tincidunt. Nullam consequat mi vitae pharetra sagittis. Suspendisse porta placerat velit, ac condimentum felis molestie in. Nullam eget velit in erat consectetur semper vitae ac nisi. Donec et lectus ut purus aliquam pulvinar non in arcu. Vestibulum et turpis a nisl placerat euismod. Aliquam eu quam augue. Cras consectetur, velit ut semper aliquam, odio tortor suscipit nulla, et vulputate dui risus at ante. Maecenas ac dignissim ex. Pellentesque in dignissim massa. Fusce at posuere lorem. Vivamus molestie nisl ac nisi rhoncus vulputate. Aenean augue arcu, maximus ut consequat in, lobortis sit amet lectus. Suspendisse dapibus auctor quam, sed tempor orci euismod accumsan. In hac habitasse platea dictumst. Suspendisse ut enim metus.</p>
    <p>Nullam at mi eros. Lorem ipsum dolor sit amet, consectetur adipiscing elit. Vestibulum tempus, sem id pharetra ultrices, magna nulla aliquet sapien, ac fringilla odio tortor in eros. Duis a urna sem. Nunc ac purus mattis, pharetra urna quis, ultrices quam. Proin ac sollicitudin dolor, ac feugiat turpis. Sed aliquet ornare nisi, vitae finibus tortor vehicula auctor.</p>
  </section>

  <div class="closing">Regards</div>
  <div class="signature" role="img" aria-label="Handwritten signature of the sender"></div>
  <div class="signer">Your Name Here<br>Designation Here</div>

  <div class="footer-rule"></div>

  <div class="contact contact-phone">
    <svg class="contact-icon" viewBox="0 0 44 44" aria-hidden="true">
      <circle cx="22" cy="22" r="22" fill="var(--brand-green)"/>
      <path d="M15 11c1.5-1 3-.5 3.6.8l1.8 3.8c.5 1 .2 2-.6 2.7l-1.5 1.3c1 2.6 3 4.8 5.6 6.2l1.4-1.4c.8-.8 1.9-1 2.8-.4l3.6 2c1.2.7 1.5 2.2.6 3.5-1.4 2-3.6 3-6 2.2-6.4-2.2-11.6-7.6-13.4-14.1-.6-2.4.4-4.9 2.1-6.6z" fill="#fff"/>
    </svg>
    <div class="contact-text">+12345689<br>+12345689</div>
  </div>

  <div class="contact contact-web">
    <svg class="contact-icon" viewBox="0 0 40 40" aria-hidden="true" fill="none" stroke="var(--brand-green)" stroke-width="2.4">
      <circle cx="20" cy="20" r="18"/>
      <ellipse cx="20" cy="20" rx="8" ry="18"/>
      <line x1="20" y1="2" x2="20" y2="38"/>
      <line x1="2" y1="20" x2="38" y2="20"/>
      <path d="M5 11h30M5 29h30"/>
    </svg>
    <div class="contact-text">www.yourwebsite.com</div>
  </div>

  <div class="contact contact-mail">
    <svg class="contact-icon" viewBox="0 0 44 44" aria-hidden="true">
      <circle cx="22" cy="22" r="22" fill="var(--brand-green)"/>
      <rect x="11" y="14" width="22" height="16" rx="1.5" fill="none" stroke="#fff" stroke-width="1.8"/>
      <path d="M11.5 15l10.5 8.5L32.5 15M11.5 29l8-7M32.5 29l-8-7" fill="none" stroke="#fff" stroke-width="1.5"/>
    </svg>
    <div class="contact-text">yourgmail@.com</div>
  </div>

  <svg class="band-accent" viewBox="0 0 360 27" preserveAspectRatio="none" aria-hidden="true">
    <polygon points="0,0 349,0 360,27 0,27" fill="var(--brand-green)"/>
  </svg>
  <div class="band-base"></div>
</main>
</body>
</html>
```